BOLD & MINIMALIST DESIGN NEEDED

We want a very bold but minimalistic business card design that is impactful and utilizes both sides of the business card. Our current logo is included for your use.

We want bold fonts and good use of negative space. We don't want the logo to overpower the design.

Target Market(s)

Professionals who are building new commercial buildings.

Industry/Entity Type

Construction

Contact Information for Business Card

Name, Title, email, office phone, cell phone, website

Font styles to use
Serif
Sans Serif

Requirements
Must have
• Bold design!

```html
<!DOCTYPE html>
<html lang="en">
<head>
<meta charset="utf-8">
<title>Ridgeline Design + Build — Business Card</title>
<link rel="stylesheet" href="https://fonts.googleapis.com/css2?family=Montserrat:wght@400;500;700;800&display=swap">
<style>
  :root {
    --backdrop: #3a3a3a;
    --card: #1c1c1c;
    --card-edge: #8fd14f;
    --accent: #8fd14f;
    --ink: #f2f2f2;
    --ink-soft: #d6d6d6;
    --gloss: #0d0d0d;
  }
  * { box-sizing: border-box; margin: 0; padding: 0; }
  html, body {
    width: 1200px; height: 791px; overflow: hidden;
    background: var(--backdrop);
    font-family: "Montserrat", Arial, sans-serif;
  }
  .stage { position: relative; width: 1200px; height: 791px; }
  .card {
    position: absolute; width: 560px; height: 320px;
    background: var(--card);
    border-bottom: 3px solid var(--card-edge);
    border-left: 3px solid var(--card-edge);
    border-radius: 2px;
  }
  .card--front { left: 40px; top: 70px; }
  .card--back { left: 600px; top: 400px; }

  .brand {
    position: absolute; left: 36px; top: 182px;
    display: flex; align-items: center; gap: 12px;
  }
  .brand__mark { width: 16px; height: 16px; background: var(--accent); flex: none; }
  .brand__name {
    color: var(--ink); font-weight: 800; font-size: 22px;
    line-height: 1.1; letter-spacing: 0.5px; text-transform: uppercase;
    white-space: nowrap;
  }
  .divider {
    position: absolute; left: 300px; top: 120px;
    width: 1.5px; height: 110px; background: var(--accent);
  }
  .contact { position: absolute; left: 322px; top: 62px; }
  .contact__name {
    color: var(--accent); font-weight: 800; font-size: 21px; letter-spacing: 0.3px;
    white-space: nowrap;
  }
  .contact__title { color: var(--ink); font-size: 14px; margin-top: 2px; }
  .contact__list { list-style: none; margin-top: 26px; }
  .contact__item {
    display: flex; align-items: center; gap: 10px;
    color: var(--ink-soft); font-size: 14px; line-height: 24px;
    white-space: nowrap;
  }
  .contact__icon { width: 13px; height: 13px; flex: none; }

  .back-name {
    position: absolute; left: 0; right: 0; top: 118px;
    text-align: center; color: var(--gloss);
    font-weight: 800; font-size: 44px; line-height: 1.05;
    letter-spacing: 1px; text-transform: uppercase;
  }
  .back-name small {
    display: block; font-size: 20px; letter-spacing: 8px; margin-top: 6px;
  }
</style>
</head>
<body>
<main class="stage">
  <section class="card card--front" aria-label="Card front">
    <div class="brand">
      <span class="brand__mark"></span>
      <span class="brand__name">Ridgeline<br>Design + Build</span>
    </div>
    <span class="divider"></span>
    <div class="contact">
      <p class="contact__name">MARTIN CALDER</p>
      <p class="contact__title">President</p>
      <ul class="contact__list">
        <li class="contact__item">
          <svg class="contact__icon" viewBox="0 0 16 16"><path fill="var(--accent)" d="M3 1l3 3-2 2c1 2 3 4 5 5l2-2 3 3-2 2C7 14 2 9 1 3z"/></svg>
          555-014-2200
        </li>
        <li class="contact__item">
          <svg class="contact__icon" viewBox="0 0 16 16"><rect x="4" y="1" width="8" height="14" rx="1.5" fill="none" stroke="var(--accent)" stroke-width="1.6"/><circle cx="8" cy="12.5" r="0.9" fill="var(--accent)"/></svg>
          555-014-2201
        </li>
        <li class="contact__item">
          <svg class="contact__icon" viewBox="0 0 16 16"><rect x="1" y="3" width="14" height="10" fill="var(--accent)"/><path d="M1 3l7 6 7-6" fill="none" stroke="var(--card)" stroke-width="1.4"/></svg>
          m.calder@r-d-b.com
        </li>
        <li class="contact__item">
          <svg class="contact__icon" viewBox="0 0 16 16"><circle cx="8" cy="8" r="6.5" fill="none" stroke="var(--accent)" stroke-width="1.6"/><path d="M1.5 8h13M8 1.5c-3 3-3 10 0 13M8 1.5c3 3 3 10 0 13" fill="none" stroke="var(--accent)" stroke-width="1.2"/></svg>
          www.r-d-b.com
        </li>
      </ul>
    </div>
  </section>

  <section class="card card--back" aria-label="Card back">
    <p class="back-name">Ridgeline<small>Design + Build</small></p>
  </section>
</main>
</body>
</html>
```